Business card design needed

Business Card design required for new small plumbing business.
Would like a logo/text look that is simple and unique and does not have to be representative of a plumbing company (ie. having a cartoon plumber or toilet etc) as the companyname is self explanatory.
Would like the main colour to be green (lime green).

Industry/Entity Type

Plumber

Contact Information for Business Card

BRAMFORD PLUMBING
ABN 71 546 190 327 004

Simon Harcastle
Licensed Plumber 83615
Phone: 0487 214 670

27 Bramford Drive,
Kellbrook. 3987 Westmere

Email: bramfordplumbing@quellmail.example

Logo Text

Bramford Plumbing

Logo styles of interest
Character Logo
Wordmark Logo
Lettermark Logo

```html
<!DOCTYPE html>
<html lang="en">
<head>
<meta charset="utf-8">
<title>Bramford Plumbing – Business Card</title>
<link rel="stylesheet" href="https://fonts.googleapis.com/css2?family=Tinos:wght@400;700&display=swap">
<style>
  :root {
    --lime: #8cc63f;
    --grey: #a7a9ab;
    --grey-light: #c2c3c5;
    --ink: #1f2a5a;
    --paper: #ffffff;
    --backdrop: #f2f2f2;
  }
  * { box-sizing: border-box; margin: 0; padding: 0; }
  html, body { width: 1200px; height: 960px; overflow: hidden; }
  body {
    background: var(--backdrop);
    font-family: "Tinos", "Times New Roman", serif;
    display: flex; align-items: center; justify-content: center;
  }
  .business-card {
    position: relative;
    width: 900px; height: 514px;
    background: var(--paper);
    overflow: hidden;
    box-shadow: 0 10px 30px rgba(0,0,0,.12);
  }
  .corner-accent { position: absolute; left: 0; top: 0; }
  .top-band {
    position: absolute; left: 470px; top: 48px; right: 0; height: 80px;
    background: var(--lime);
  }
  .logo-pill {
    position: absolute; left: 110px; top: 30px;
    width: 420px; height: 96px;
    background: var(--grey-light);
    border-radius: 48px;
    display: flex; align-items: center; gap: 14px;
    padding-left: 40px;
  }
  .logo-mark { flex: none; width: 20px; height: 20px; border-radius: 50%; background: var(--ink); }
  .logo-name {
    font-weight: 700; font-size: 28px; letter-spacing: 1px;
    color: var(--ink); white-space: nowrap;
  }
  .ornament {
    position: absolute; left: 40px; top: 160px;
    width: 320px; height: 300px;
    background: radial-gradient(ellipse at 45% 45%, #b6dc7c 0%, #d6ebb6 45%, #ffffff 75%);
    border-radius: 40%;
  }
  .details-panel {
    position: absolute; left: 420px; top: 128px; right: 0; height: 150px;
    background: var(--grey);
    padding: 22px 36px 0 42px;
    color: var(--ink);
  }
  .person-name { font-size: 30px; font-weight: 400; margin-bottom: 12px; }
  .details-panel p { font-size: 16px; line-height: 1.35; }
  .contact-panel {
    position: absolute; left: 420px; top: 278px; right: 0; bottom: 0;
    background: var(--lime);
    padding: 40px 36px 0 42px;
    color: var(--ink);
  }
  .contact-panel p { font-size: 16px; line-height: 1.5; }
</style>
</head>
<body>
  <article class="business-card">
    <svg class="corner-accent" width="70" height="70" viewBox="0 0 70 70" aria-hidden="true">
      <polygon points="0,0 70,0 0,70" fill="var(--lime)"/>
    </svg>

    <div class="top-band"></div>

    <header class="logo-pill">
      <span class="logo-mark"></span>
      <span class="logo-name">BRAMFORD PLUMBING</span>
    </header>

    <div class="ornament" role="img" aria-label="Decorative floral swirl ornament in black and lime green"></div>

    <section class="details-panel">
      <h1 class="person-name">Simon Harcastle</h1>
      <p>Licensed Plumber 83615</p>
      <p>Phone: 0487 214 670</p>
      <p>27 Bramford Drive, Kellbrook 3987 Westmere</p>
    </section>

    <section class="contact-panel">
      <p>ABN 71 546 190 327 004</p>
      <p>Email: bramfordplumbing@quellmail.example</p>
    </section>
  </article>
</body>
</html>
```